Duct Manufacturing Company new to the industry needs business card and stationary design

we are sheet metal duct manufacturers looking for a business card design to fit my new business logo.
nothing to crazy that will date, but want it to stand out from the crowed.
I'm sure you guys will work it out.

Contact Information for Business Card

Glen Marsh
Director

Address
17 Dorwell St
Corrandale NSW 2631

0438 760 514

Sales@flowbend.com.au

Font styles to use
Other font styles liked:
• BankGothic md bt

Requirements
Nice to have
• Like the idea of corner rounded to match logo
• like to keep colours flowing
• font I like sharp square not rounded

```html
<!DOCTYPE html>
<html lang="en">
<head>
<meta charset="utf-8">
<title>Flowbend Industries – Business Card</title>
<link href="https://fonts.googleapis.com/css2?family=Michroma&family=Montserrat:wght@400;500&display=swap" rel="stylesheet">
<style>
  :root {
    --backdrop: #e4e4e4;
    --card: #0b0b0c;
    --card-edge: #1a1a1c;
    --brand-green: #7dc242;
    --brand-blue: #1e8fdc;
    --text-light: #f1f1f1;
    --text-muted: #c9c9c9;
  }
  * { box-sizing: border-box; margin: 0; padding: 0; }
  html, body {
    width: 1200px; height: 1200px; overflow: hidden;
    background: var(--backdrop);
  }
  .sheet {
    position: relative; width: 1200px; height: 1200px;
    display: flex; flex-direction: column; align-items: center; justify-content: center; gap: 70px;
  }
  .card {
    position: relative;
    width: 760px; height: 460px;
    border-radius: 28px;
    background: linear-gradient(135deg, var(--card-edge) 0%, var(--card) 45%, var(--card) 100%);
    box-shadow: 0 14px 30px rgba(0,0,0,0.25);
    overflow: hidden;
  }
  .brand {
    display: flex; align-items: center; gap: 18px;
    font-family: "Michroma", sans-serif;
    color: var(--brand-green);
    letter-spacing: 2px;
  }
  .brand-dot {
    width: 26px; height: 26px; border-radius: 50%;
    background: var(--brand-blue);
    flex: none;
  }
  .card-front { display: flex; align-items: center; justify-content: center; }
  .card-front .brand { font-size: 38px; line-height: 1.25; }
  .card-back .brand {
    position: absolute; left: 60px; top: 200px;
    font-size: 26px; line-height: 1.3;
  }
  .contact {
    position: absolute; left: 420px; top: 80px;
    font-family: "Montserrat", sans-serif; color: var(--text-light);
  }
  .contact-name {
    font-family: "Michroma", sans-serif; font-weight: 400;
    color: var(--brand-blue); font-size: 26px; letter-spacing: 2px;
  }
  .contact-role { color: var(--text-muted); font-size: 17px; margin: 6px 0 30px; }
  .contact-list { list-style: none; font-size: 18px; line-height: 1.55; }
  .contact-list li { display: flex; align-items: flex-start; gap: 14px; }
  .contact-list svg { width: 18px; height: 18px; margin-top: 4px; flex: none; fill: var(--brand-blue); }
  .contact-list .no-icon { padding-left: 32px; }
</style>
</head>
<body>
<main class="sheet">
  <section class="card card-front">
    <div class="brand">
      <span class="brand-dot"></span>
      <span>FLOWBEND<br>INDUSTRIES</span>
    </div>
  </section>

  <section class="card card-back">
    <div class="brand">
      <span class="brand-dot"></span>
      <span>FLOWBEND<br>INDUSTRIES</span>
    </div>
    <div class="contact">
      <h1 class="contact-name">GLEN MARSH</h1>
      <p class="contact-role">Director</p>
      <ul class="contact-list">
        <li><svg viewBox="0 0 24 24" aria-hidden="true"><path d="M6.6 10.8a15.1 15.1 0 0 0 6.6 6.6l2.2-2.2a1 1 0 0 1 1-.25 11.4 11.4 0 0 0 3.6.57 1 1 0 0 1 1 1V20a1 1 0 0 1-1 1A17 17 0 0 1 3 4a1 1 0 0 1 1-1h3.5a1 1 0 0 1 1 1c0 1.25.2 2.45.57 3.6a1 1 0 0 1-.25 1z"/></svg><span>0438 760 514</span></li>
        <li><svg viewBox="0 0 24 24" aria-hidden="true"><path d="M12 2a10 10 0 1 0 0 20 10 10 0 0 0 0-20zm6.9 6h-2.9a15.6 15.6 0 0 0-1.4-3.6A8 8 0 0 1 18.9 8zM12 4c.8 1.2 1.5 2.5 1.9 4h-3.8c.4-1.5 1.1-2.8 1.900-4zM4.3 14a8 8 0 0 1 0-4h3.4a16.5 16.5 0 0 0 0 4zm.8 2h2.9c.3 1.3.8 2.5 1.4 3.6A8 8 0 0 1 5.1 16zM8 8H5.1a8 8 0 0 1 4.3-3.6C8.8 5.5 8.3 6.7 8 8zm4 12c-.8-1.2-1.5-2.5-1.9-4h3.8c-.4 1.5-1.1 2.8-1.9 4zm2.3-6H9.7a14.7 14.7 0 0 1 0-4h4.6a14.7 14.7 0 0 1 0 4zm.3 5.6c.6-1.1 1.1-2.3 1.4-3.6h2.9a8 8 0 0 1-4.3 3.6zM16.3 14a16.5 16.5 0 0 0 0-4h3.4a8 8 0 0 1 0 4z"/></svg><span>flowbend.com.au</span></li>
        <li><svg viewBox="0 0 24 24" aria-hidden="true"><path d="M3 5h18a1 1 0 0 1 1 1v12a1 1 0 0 1-1 1H3a1 1 0 0 1-1-1V6a1 1 0 0 1 1-1zm9 7.2L4.5 7v1.9L12 14l7.5-5.1V7z"/></svg><span>Sales@flowbend.com.au</span></li>
        <li class="no-icon"><span>17 Dorwell St<br>Corrandale NSW 2631</span></li>
      </ul>
    </div>
  </section>
</main>
</body>
</html>
```